Moravel Aesthetic Doctor

I require an elegant, luxurious looking business card for my aesthetic business. I am a doctor and that will set me aside from competitors. I am planning to provide home and spa based treatments to clients with high expectations. I have attached my logo.

```html
<!DOCTYPE html>
<html lang="en">
<head>
<meta charset="utf-8">
<title>Moravel Aesthetic Doctor – Business Card</title>
<link href="https://fonts.googleapis.com/css2?family=Roboto:wght@300;400;500&display=swap" rel="stylesheet">
<style>
  :root {
    --page: #d6d6d4;
    --card: #ffffff;
    --deep-blue: #1d6db5;
    --mid-blue: #3497d4;
    --sky-blue: #5bb8e8;
    --pale-blue: #a9dcf3;
    --soft-grey: #a4a6a8;
    --text-grey: #9a9a9a;
    --white: #ffffff;
  }
  * { margin: 0; padding: 0; box-sizing: border-box; }
  html, body { width: 1125px; height: 1200px; overflow: hidden; background: var(--page); }
  body { position: relative; font-family: "Roboto", Arial, sans-serif; }

  .card {
    position: absolute; left: 151px; width: 824px; height: 470px;
    background: var(--card); border-radius: 22px; overflow: hidden;
    box-shadow: 0 3px 6px rgba(0,0,0,0.18);
  }
  .card--front { top: 99px; }
  .card--back { top: 631px; }
  .card svg.shapes { position: absolute; inset: 0; width: 100%; height: 100%; }

  /* Front */
  .holder { position: absolute; right: 35px; top: 34px; text-align: right; }
  .holder__name { font-size: 29px; font-weight: 500; color: var(--sky-blue); }
  .holder__post { font-size: 18px; font-weight: 400; }
  .holder__title { margin-top: 6px; font-size: 20px; font-weight: 300; color: var(--text-grey); }

  .brand { position: absolute; left: 46px; top: 118px; display: flex; align-items: center; gap: 30px; }
  .brand__dot { width: 112px; height: 112px; border-radius: 50%; border: 3px solid var(--soft-grey); }
  .brand__name { color: var(--sky-blue); font-weight: 400; line-height: 1.08; text-transform: uppercase; }
  .brand__name .big { display: block; font-size: 52px; letter-spacing: 2px; }
  .brand__name .small { display: block; font-size: 24px; letter-spacing: 1.5px; }

  .social { position: absolute; right: 36px; top: 292px; display: flex; gap: 20px; }
  .social span { width: 25px; height: 25px; border-radius: 50%; background: var(--white); }

  .contact { position: absolute; right: 32px; top: 330px; list-style: none; color: var(--white); font-size: 21px; font-weight: 300; }
  .contact li { display: flex; justify-content: flex-end; align-items: center; gap: 12px; height: 33px; }
  .contact svg { width: 20px; height: 20px; }

  /* Back */
  .back-brand { position: absolute; right: 39px; top: 50px; color: var(--white); font-weight: 400; text-align: center; text-transform: uppercase; line-height: 1.08; }
  .back-brand .big { display: block; font-size: 50px; letter-spacing: 1.5px; }
  .back-brand .small { display: block; font-size: 23px; letter-spacing: 1px; }

  .services { position: absolute; left: 553px; top: 185px; list-style: none; color: var(--white); font-size: 21.5px; font-weight: 300; }
  .services li { position: relative; padding-left: 17px; line-height: 33px; }
  .services li::before { content: ""; position: absolute; left: 0; top: 12px; width: 9px; height: 9px; border-radius: 50%; background: var(--white); }
</style>
</head>
<body>

<section class="card card--front">
  <svg class="shapes" viewBox="0 0 824 470" preserveAspectRatio="none" aria-hidden="true">
    <path d="M0 396 C 230 430, 430 380, 600 290 C 690 245, 760 226, 824 230 L824 470 L0 470 Z" fill="var(--deep-blue)"/>
    <path d="M0 345 C 170 345, 330 315, 490 248 C 360 300, 200 342, 0 380 Z" fill="var(--soft-grey)"/>
    <path d="M118 428 C 320 390, 520 300, 700 190 C 520 290, 330 370, 118 428 Z" fill="var(--white)"/>
    <path d="M118 420 C 330 385, 520 290, 700 190 C 520 300, 320 395, 118 420 Z" fill="var(--deep-blue)"/>
  </svg>

  <div class="holder">
    <p class="holder__name">Dr Elin Varsk, <span class="holder__post">MRCPCH MD</span></p>
    <p class="holder__title">Australasian Diploma of Aesthetic Medicine</p>
  </div>

  <div class="brand">
    <span class="brand__dot"></span>
    <p class="brand__name"><span class="big">Moravel</span><span class="small">Aesthetic Doctor</span></p>
  </div>

  <div class="social" aria-label="Social profiles"><span></span><span></span></div>

  <ul class="contact">
    <li>0800 437 219
      <svg viewBox="0 0 24 24" aria-hidden="true"><path d="M6.6 10.8a15 15 0 0 0 6.6 6.6l2.2-2.2a1 1 0 0 1 1-.25 11 11 0 0 0 3.6.6 1 1 0 0 1 1 1V20a1 1 0 0 1-1 1A17 17 0 0 1 3 4a1 1 0 0 1 1-1h3.5a1 1 0 0 1 1 1 11 11 0 0 0 .6 3.6 1 1 0 0 1-.25 1z" fill="#fff"/></svg></li>
    <li>elin@moravel.co.nz
      <svg viewBox="0 0 24 24" aria-hidden="true"><rect x="3" y="6" width="18" height="13" rx="2" fill="none" stroke="#fff" stroke-width="2"/><path d="M4 7l8 6 8-6" fill="none" stroke="#fff" stroke-width="2"/></svg></li>
    <li>www.moravel.co.nz
      <svg viewBox="0 0 24 24" aria-hidden="true"><g fill="none" stroke="#fff" stroke-width="1.6"><circle cx="12" cy="12" r="9"/><ellipse cx="12" cy="12" rx="4" ry="9"/><path d="M3 12h18M5 7h14M5 17h14"/></g></svg></li>
  </ul>
</section>

<section class="card card--back">
  <svg class="shapes" viewBox="0 0 824 470" preserveAspectRatio="none" aria-hidden="true">
    <defs>
      <linearGradient id="artTone" x1="0" y1="0" x2="1" y2="1">
        <stop offset="0" stop-color="var(--pale-blue)"/>
        <stop offset="1" stop-color="var(--sky-blue)"/>
      </linearGradient>
    </defs>
    <rect width="824" height="470" fill="var(--mid-blue)"/>
    <path d="M0 0 L334 0 A 241 241 0 0 1 334 470 L0 470 Z" fill="var(--white)"/>
  </svg>
  <svg class="shapes" viewBox="0 0 824 470" preserveAspectRatio="none" role="img" aria-label="Flowing blue illustration of the brand artwork">
    <rect x="0" y="40" width="420" height="390" rx="24" fill="url(#artTone)"/>
  </svg>

  <p class="back-brand"><span class="big">Moravel</span><span class="small">Aesthetic Doctor</span></p>

  <ul class="services">
    <li>Dermal injectables</li>
    <li>Plasma facials</li>
    <li>Microneedling</li>
    <li>Skin boosters</li>
    <li>Excessive sweating</li>
    <li>Home and Spa Based<br>Treatments</li>
  </ul>
</section>

</body>
</html>
```